Bry7Legal Letterhead

Need a new letterhead for my law firm.
IDENTIFYING INFORMATION BELOW:
Anselmo R Quintara III
Attorney at Law
Address: 2847 Larkspur Blvd, Ste 300, Dallas, TX 75204
Phone: 877-482-6017
Fax: 469-738-1452
Email: bry@bry7legal.example
Website: www.bry7legal.example

Colors
0054AA
0677BA
7BADD7
CADEEF
E8F1F8

Requirements
Must have
• Logo needs to be on the letterhead, along with identifying information which is included in the project description.

```html
<!DOCTYPE html>
<html lang="en">
<head>
<meta charset="utf-8">
<title>Bry7Legal Letterhead</title>
<link href="https://fonts.googleapis.com/css2?family=Montserrat:wght@300;400;600;700&display=swap" rel="stylesheet">
<style>
  :root {
    --backdrop: #e4e4e4;
    --paper: #ffffff;
    --ink: #1b1b1b;
    --ink-soft: #3a3a3a;
    --rule: #8a8a8a;
    --blue-deep: #0054AA;
    --blue-mid: #0677BA;
    --blue-bright: #1a9ad6;
    --band: #161616;
  }
  html, body {
    margin: 0;
    width: 1200px;
    height: 874px;
    overflow: hidden;
    background: var(--backdrop);
    font-family: "Montserrat", sans-serif;
  }
  .letterhead {
    position: absolute;
    left: 302px;
    top: 16px;
    width: 596px;
    height: 842px;
    background: var(--paper);
    box-shadow: 0 6px 24px rgba(0,0,0,0.12);
    overflow: hidden;
  }
  .brand {
    position: absolute;
    left: 52px;
    top: 70px;
  }
  .brand-name {
    margin: 0;
    font-weight: 700;
    font-size: 32px;
    letter-spacing: 1px;
    color: var(--ink);
    line-height: 1;
    text-transform: uppercase;
  }
  .brand-tagline {
    margin: 4px 0 0 50px;
    font-weight: 300;
    font-size: 12.5px;
    letter-spacing: 2.4px;
    color: var(--ink-soft);
    text-transform: uppercase;
  }
  .contact {
    position: absolute;
    left: 372px;
    top: 34px;
    padding-left: 12px;
    border-left: 1px solid var(--rule);
    font-size: 9.5px;
    font-style: normal;
    line-height: 1.35;
    color: var(--ink);
  }
  .contact p { margin: 0; }
  .contact .attorney-name { font-weight: 600; font-size: 10px; }
  .contact .attorney-title { color: var(--blue-mid); margin-bottom: 3px; }
  .contact-line {
    display: flex;
    align-items: center;
    gap: 5px;
  }
  .contact-line svg { width: 8px; height: 8px; fill: var(--blue-mid); flex: none; }
  .footer-band {
    position: absolute;
    left: 0;
    bottom: 0;
    width: 596px;
    height: 70px;
  }
  .web {
    position: absolute;
    right: 18px;
    bottom: 21px;
    display: flex;
    align-items: center;
    gap: 6px;
    color: #ffffff;
    font-size: 10.5px;
    letter-spacing: 0.2px;
    white-space: nowrap;
  }
  .web svg { width: 10px; height: 10px; flex: none; }
</style>
</head>
<body>
  <main class="letterhead">
    <header class="brand">
      <h1 class="brand-name">Bry7Legal</h1>
      <p class="brand-tagline">Stand with Bry</p>
    </header>

    <address class="contact">
      <p class="attorney-name">Anselmo R Quintara III</p>
      <p class="attorney-title">Attorney at Law</p>
      <p>2847 Larkspur Blvd, Ste</p>
      <p>300, Dallas, TX 75204</p>
      <p class="contact-line">
        <svg viewBox="0 0 10 10" aria-hidden="true"><path d="M2 0.5 L4 2.5 L3 3.8 Q4.5 6 6.2 7 L7.5 6 L9.5 8 L8 9.5 Q3.5 9 0.5 2 Z"/></svg>
        <span>877-482-6017</span>
      </p>
      <p class="contact-line">
        <svg viewBox="0 0 10 10" aria-hidden="true"><rect x="2.5" y="0.5" width="5" height="3"/><rect x="0.5" y="4" width="9" height="4.5" rx="1"/><rect x="2.5" y="7" width="5" height="2.5" fill="#fff"/></svg>
        <span>469-738-1452</span>
      </p>
      <p class="contact-line">
        <svg viewBox="0 0 10 10" aria-hidden="true"><rect x="0.5" y="2" width="9" height="6.5"/><path d="M0.5 2 L5 5.8 L9.5 2" fill="none" stroke="#fff" stroke-width="1"/></svg>
        <span>bry@bry7legal.example</span>
      </p>
    </address>

    <svg class="footer-band" viewBox="0 0 596 70" aria-hidden="true">
      <defs>
        <linearGradient id="stripe-blue" x1="0" y1="0" x2="1" y2="0">
          <stop offset="0" stop-color="#0054AA"/>
          <stop offset="0.6" stop-color="#0677BA"/>
          <stop offset="1" stop-color="#1a9ad6"/>
        </linearGradient>
      </defs>
      <polygon points="0,36 410,36 406,48 0,48" fill="url(#stripe-blue)"/>
      <polygon points="0,56 408,56 424,10 596,10 596,70 0,70" fill="#161616"/>
    </svg>

    <div class="web">
      <svg viewBox="0 0 10 10" aria-hidden="true"><circle cx="5" cy="5" r="4.5" fill="#fff"/><path d="M2.5 3 Q4 2 5 3.5 Q4 5 5.5 6 Q5 8 3.5 8.5 Q2 6 2.5 3Z M6.5 1.5 Q8.5 3 8 5 Q7 4.5 6.5 1.5Z" fill="#161616"/></svg>
      <span>www.bry7legal.example</span>
    </div>
  </main>
</body>
</html>
```